Design Startseite Kanzlei-Homepage
Zielgruppe
Wir sind eine Rechtsanwaltskanzlei in Kempten (Allgäu) und regional sowie überregional in verschiedenen Rechtsgebieten tätig. Unsere Zielgruppe sind sowohl private als auch gewerbliche Mandanten.
Aufgabenstellung
Die bestehende Gestaltung wirkt derzeit aus unserer Sicht überholt. Insbesondere soll das bislang dominierende Rot vollständig entfallen.
Stattdessen stellen wir uns ein modernes, hochwertiges Erscheinungsbild vor, primär in dunklen Farbtönen (Anthrazit/Schwarz) kombiniert mit Beige- bzw. warmen Naturtönen. Ziel ist eine klare visuelle Anlehnung an unsere Kanzleiräumlichkeiten (siehe Fotos).
Die Webseite soll insgesamt moderner, klarer und visuell anspruchsvoller wirken, ohne an Seriosität und Zugänglichkeit einzubüßen. Die Balance zwischen hochwertigem Erscheinungsbild und mandantenorientierter Nutzerführung steht für uns im Vordergrund.

```html
<!DOCTYPE html>
<html lang="de">
<head>
<meta charset="utf-8">
<title>Kanzlei am Lindenhof – Rechtsanwälte in Kempten</title>
<link href="https://fonts.googleapis.com/css2?family=Urbanist:wght@300;400;500;600&family=Inter:wght@400;500;600;700&display=swap" rel="stylesheet">
<style>
:root{
  --ink:#1b1a18;
  --ink-2:#24221f;
  --ink-3:#2e2b27;
  --cream:#fcf8ee;
  --cream-2:#f6f0e2;
  --line:#e8dfcc;
  --gold:#c8a96b;
  --gold-soft:#d8bf8a;
  --text:#2a2824;
  --muted:#77716a;
  --white:#ffffff;
}
*{box-sizing:border-box;margin:0;padding:0}
html,body{width:1200px;height:3974px;overflow:hidden}
body{background:var(--cream);font-family:"Inter",sans-serif;color:var(--text);font-size:8px;line-height:1.55;position:relative}
.abs{position:absolute}
.display{font-family:"Urbanist",sans-serif;font-weight:400;letter-spacing:-0.045em;line-height:1}
.eyebrow{font-size:6px;letter-spacing:.28em;text-transform:uppercase;color:var(--gold);font-weight:600}
.btn{display:inline-flex;align-items:center;gap:6px;height:25px;padding:0 13px;font-size:7.5px;font-weight:600;border:1px solid currentColor;white-space:nowrap}
.btn svg{width:7px;height:7px}
.btn-dark{color:var(--white);border-color:rgba(255,255,255,.45)}
.btn-gold{color:var(--white);border-color:var(--gold)}
.btn-line{color:var(--text);border-color:var(--line);height:20px;padding:0 9px;font-size:7px;background:var(--white)}

/* top bar + nav */
.topbar{left:0;top:0;width:1200px;height:16px;background:var(--gold-soft);font-size:6.5px;text-align:center;line-height:16px;color:var(--ink)}
.nav{left:0;top:16px;width:1200px;height:41px;z-index:2;display:flex;align-items:center;padding:0 37px;color:var(--white)}
.brand{font-family:"Inter",sans-serif;font-weight:700;font-size:15px;letter-spacing:.01em;color:inherit}
.nav ul{list-style:none;display:flex;gap:18px;margin-left:auto;font-size:7px;font-weight:500}
.nav .icon-box{width:24px;height:24px;border:1px solid rgba(255,255,255,.5);margin-left:26px;display:grid;place-items:center}

/* hero */
.hero{left:0;top:16px;width:1200px;height:596px;background:linear-gradient(115deg,#2a2117 0%,#3b2e22 35%,#5a554e 60%,#2a2620 100%)}
.hero-shade{left:0;top:16px;width:1200px;height:596px;background:linear-gradient(90deg,rgba(15,13,11,.82) 0%,rgba(15,13,11,.35) 55%,rgba(15,13,11,.55) 100%)}
.hero h1{left:37px;top:345px;font-size:60px;color:var(--white)}
.hero-sub{left:37px;top:467px;width:340px;font-size:9.5px;color:#e7e1d6;line-height:1.65}
.hero-info{left:966px;top:427px;width:197px;height:103px;background:rgba(30,27,24,.75);border:1px solid rgba(255,255,255,.12);padding:14px 16px;color:var(--white)}
.hero-info h3{font-family:"Urbanist",sans-serif;font-weight:400;font-size:16px;margin:5px 0 8px}
.hero-info p{font-size:7px;color:#d3ccc0;line-height:1.7}
.hero-tabs{left:37px;top:580px;width:1126px;display:grid;grid-template-columns:repeat(4,1fr);gap:14px;color:var(--white);font-size:6px}
.hero-tabs div{padding-bottom:6px;border-bottom:1px solid rgba(255,255,255,.28)}
.hero-tabs b{color:var(--gold);margin-right:5px}
.hero-tabs .on{border-bottom:2px solid var(--white)}

/* sections */
.band-dark{left:0;width:1200px;background:var(--ink)}
h2.display{font-size:36px}
.card-grid{display:grid;grid-template-columns:repeat(3,220px);gap:8px}
.area{height:150px;background:var(--white);border:1px solid var(--line);padding:14px 16px;position:relative}
.area .num{font-size:7px;color:var(--gold);font-weight:600}
.area h3{font-family:"Urbanist",sans-serif;font-weight:500;font-size:15px;letter-spacing:-.02em;margin:23px 0 9px}
.area p{font-size:6.8px;color:var(--muted);line-height:1.75;height:27px}
.area .btn-line{position:absolute;left:16px;bottom:23px}

.check{display:flex;align-items:center;gap:8px;font-size:7.2px;color:#e4ddd0;margin-bottom:6px}
.check svg{width:10px;height:10px}

.review{width:189px;height:190px;background:rgba(58,52,46,.92);padding:18px 18px;color:var(--white);position:absolute;top:2262px}
.review .q{font-family:"Urbanist",sans-serif;font-size:22px;color:var(--gold);line-height:.6;font-weight:600}
.review .stars{color:var(--gold);font-size:10px;letter-spacing:2px;margin:5px 0 12px}
.review p{font-size:11.5px;font-weight:700;line-height:1.3;letter-spacing:-.01em}
.review small{position:absolute;left:18px;bottom:18px;font-size:6.8px;color:#d1c9bd}
.arrow-btn{width:24px;height:24px;display:grid;place-items:center;position:absolute;top:2350px}

.post{width:220px;height:267px;background:var(--white);border:1px solid var(--line);position:relative}
.post .img{height:116px}
.post .date{font-size:6px;color:var(--gold);font-weight:600;margin:12px 14px 0;display:flex;gap:5px;align-items:center}
.post h3{font-family:"Urbanist",sans-serif;font-weight:500;font-size:14px;letter-spacing:-.02em;line-height:1.05;margin:10px 14px 7px}
.post p{font-size:6.6px;color:var(--muted);line-height:1.75;margin:0 14px}
.post .btn-line{position:absolute;left:14px;bottom:26px}

.contact-line{display:flex;align-items:center;gap:9px;font-size:7.5px;font-weight:600;margin-bottom:7px}
.contact-line svg{width:10px;height:10px}

.footer{left:0;top:3724px;width:1200px;height:250px;background:var(--ink);color:var(--white)}
.fcol{position:absolute;top:46px;font-size:7px;color:#d4cdc1;line-height:2.35}
.fcol h4{font-size:5.8px;letter-spacing:.28em;color:var(--gold);font-weight:600;margin-bottom:6px;line-height:1}
.social{width:14px;height:14px;border:1px solid rgba(255,255,255,.35);display:inline-block;margin-right:4px}
</style>
</head>
<body>

<div class="abs topbar">Infos und Terminvereinbarung: <b>0831 - 540 272 10</b> oder über das <b>Kontaktformular</b></div>

<!-- Hero -->
<div class="abs hero" role="img" aria-label="Foto des Empfangsbereichs der Kanzlei mit Holzvertäfelung und Empfangstresen"></div>
<div class="abs hero-shade"></div>
<header class="abs nav">
  <span class="brand">KANZLEI LINDENHOF</span>
  <ul><li>Rechtsgebiete</li><li>Kanzlei</li><li>Bewertungen</li></ul>
  <span class="icon-box"><svg width="9" height="9" viewBox="0 0 10 10" fill="none" stroke="#fff" stroke-width="1"><circle cx="5" cy="5" r="3.8"/></svg></span>
</header>
<div class="abs eyebrow" style="left:37px;top:329px">Familienrecht · Unterhalt · Scheidung</div>
<section class="hero" style="position:static">
  <h1 class="abs display">Besonnen im<br>Familienrecht.</h1>
</section>
<p class="abs hero-sub">Fachkundige und lösungsorientierte Beratung bei Trennung, Scheidung, Unterhalt, Sorge- und Umgangsrecht.</p>
<div class="abs" style="left:37px;top:517px;display:flex;gap:6px">
  <span class="btn btn-dark">Beratung anfragen <svg viewBox="0 0 8 8" fill="none" stroke="currentColor"><path d="M2 6 6 2M3 2h3v3"/></svg></span>
  <span class="btn btn-dark"><svg viewBox="0 0 8 8" fill="none" stroke="currentColor"><path d="M2 1.5v5l4.5-2.5z"/></svg> Kanzlei ansehen</span>
</div>
<aside class="abs hero-info">
  <div class="eyebrow" style="font-size:5.5px">Kanzlei am Lindenhof</div>
  <h3>Lindenstraße 14</h3>
  <p>Rechtsanwälte in Kempten mit Beratung für private und gewerbliche Mandanten.</p>
</aside>
<nav class="abs hero-tabs">
  <div><b>01</b>Kempten</div>
  <div><b>02</b>Stark bei Kündigung und Konflikt</div>
  <div class="on"><b>03</b>Besonnen im Familienrecht</div>
  <div><b>04</b>Schnelle Hilfe im Verkehrsrecht</div>
</nav>

<!-- Intro -->
<div class="abs eyebrow" style="left:262px;top:673px">Rechtsanwälte in Kempten</div>
<h2 class="abs display" style="left:262px;top:692px">Kanzlei am Lindenhof.</h2>
<p class="abs" style="left:589px;top:677px;width:350px;font-size:8px;color:var(--muted);line-height:1.9">Die Kanzlei am Lindenhof berät private und gewerbliche Mandanten in zentralen Rechtsgebieten – mit persönlicher Betreuung, fachlicher Erfahrung und kurzfristigen Terminen.</p>
<div class="abs" style="left:262px;top:786px;width:675px;height:1px;background:var(--line)"></div>

<!-- Rechtsgebiete -->
<div class="abs eyebrow" style="left:262px;top:841px">Unsere Rechtsgebiete</div>
<h2 class="abs display" style="left:262px;top:858px">Klare Schwerpunkte.</h2>
<div class="abs card-grid" style="left:262px;top:915px;row-gap:14px">
  <article class="area"><div class="num">01</div><h3>Arbeitsrecht</h3><p>Beratung und Vertretung für Arbeitnehmer, Arbeitgeber, Betriebsräte und leitende Angestellte.</p><span class="btn btn-line">Anfrage stellen ↗</span></article>
  <article class="area"><div class="num">02</div><h3>Familienrecht</h3><p>Lösungsorientierte Begleitung bei Scheidung, Unterhalt, Sorge- und Umgangsrecht.</p><span class="btn btn-line">Anfrage stellen ↗</span></article>
  <article class="area"><div class="num">03</div><h3>Verkehrsrecht</h3><p>Kompetente Hilfe bei Unfall, Bußgeld, Fahrverbot, Autokauf und Versicherung.</p><span class="btn btn-line">Anfrage stellen ↗</span></article>
  <article class="area"><div class="num">04</div><h3>Strafrecht</h3><p>Engagierte Verteidigung mit klarem Blick für Strategie, Fristen und Verfahren.</p><span class="btn btn-line">Anfrage stellen ↗</span></article>
  <article class="area"><div class="num">05</div><h3>Erbrecht</h3><p>Beratung zu Testament, Pflichtteil, Nachlass und Erbauseinandersetzung.</p><span class="btn btn-line">Anfrage stellen ↗</span></article>
  <article class="area"><div class="num">06</div><h3>Mietrecht</h3><p>Unterstützung bei Mietvertrag, Mängeln, Kündigung und Wohnungseigentum.</p><span class="btn btn-line">Anfrage stellen ↗</span></article>
</div>

<!-- Kanzlei -->
<section class="abs band-dark" style="top:1287px;height:425px"></section>
<div class="abs" role="img" aria-label="Teamfoto der Rechtsanwältinnen, Rechtsanwälte und Mitarbeitenden der Kanzlei" style="left:262px;top:1346px;width:352px;height:309px;background:linear-gradient(180deg,#9a9893 0%,#6b6862 45%,#2c2a27 100%)"></div>
<div class="abs" style="left:280px;top:1592px;color:var(--white)">
  <div class="eyebrow" style="font-size:5.5px">Team</div>
  <div class="display" style="font-size:19px;margin-top:5px">Erfahren. Nahbar. Verlässlich.</div>
</div>
<div class="abs" style="left:280px;top:1640px;width:316px;height:1px;background:rgba(255,255,255,.3)"></div>
<div class="abs" style="left:522px;top:1639px;width:30px;height:2px;background:var(--white)"></div>
<div class="abs" style="left:281px;top:1490px;width:16px;height:16px;border-radius:50%;background:rgba(0,0,0,.35)"></div>
<div class="abs" style="left:580px;top:1490px;width:16px;height:16px;border-radius:50%;background:rgba(0,0,0,.35)"></div>
<div class="abs eyebrow" style="left:652px;top:1406px">Die Kanzlei</div>
<h2 class="abs display" style="left:652px;top:1424px;color:var(--white)">Ruhige Räume.<br>Klare Beratung.</h2>
<p class="abs" style="left:652px;top:1506px;width:285px;font-size:7.8px;color:#d4cdc1;line-height:1.8">In Kempten zuhause, im Allgäu und überregional tätig: Die Kanzlei verbindet persönliche Beratung mit engagierter Interessenvertretung.</p>
<div class="abs" style="left:652px;top:1548px">
  <div class="check"><svg viewBox="0 0 10 10" fill="none" stroke="#c8a96b"><circle cx="5" cy="5" r="4.3"/><path d="M3 5.1 4.4 6.5 7 3.7"/></svg>Kurzfristige Termine möglich</div>
  <div class="check"><svg viewBox="0 0 10 10" fill="none" stroke="#c8a96b"><circle cx="5" cy="5" r="4.3"/><path d="M3 5.1 4.4 6.5 7 3.7"/></svg>Beratung für Privatpersonen und Unternehmen</div>
  <div class="check"><svg viewBox="0 0 10 10" fill="none" stroke="#c8a96b"><circle cx="5" cy="5" r="4.3"/><path d="M3 5.1 4.4 6.5 7 3.7"/></svg>Fachanwaltliche Erfahrung in mehreren Rechtsgebieten</div>
</div>

<!-- Persönlich -->
<div class="abs" role="img" aria-label="Videovorschau mit Blick in den Empfangsbereich der Kanzlei" style="left:262px;top:1772px;width:386px;height:262px;background:linear-gradient(160deg,#cfcac2 0%,#8a6d4e 45%,#2d2823 100%)"></div>
<div class="abs" style="left:434px;top:1884px;width:40px;height:40px;background:var(--white);display:grid;place-items:center"><svg width="11" height="11" viewBox="0 0 10 10"><path d="M2.5 1.5v7l6-3.5z" fill="#1b1a18"/></svg></div>
<div class="abs eyebrow" style="left:680px;top:1829px">Kanzlei in Kempten</div>
<h2 class="abs display" style="left:680px;top:1845px">Persönlich<br>erreichbar.</h2>
<p class="abs" style="left:680px;top:1928px;width:250px;font-size:7.8px;color:var(--muted);line-height:1.9">Ob Arbeitsrecht, Familienrecht, Erbrecht, Verkehrsrecht, Strafrecht oder Mietrecht: Die Kanzlei am Lindenhof bietet klare Orientierung und verlässliche Vertretung.</p>

<!-- Bewertungen -->
<section class="abs" role="img" aria-label="Abgedunkeltes Foto eines Besprechungsraums der Kanzlei" style="left:0;top:2093px;width:1200px;height:431px;background:radial-gradient(ellipse at 50% 40%,#3b3630 0%,#22201d 60%,#151412 100%)"></section>
<div class="abs eyebrow" style="left:0;top:2147px;width:1200px;text-align:center">Mandantenstimmen</div>
<h2 class="abs display" style="left:0;top:2164px;width:1200px;text-align:center;color:var(--white)">Bewertungen mit<br>Substanz.</h2>
<div class="arrow-btn" style="left:270px;border:1px solid rgba(255,255,255,.35)"><svg width="8" height="8" viewBox="0 0 8 8" fill="none" stroke="#fff"><path d="M5 1.5 2.5 4 5 6.5"/></svg></div>
<article class="review" style="left:308px"><div class="q">99</div><div class="stars">★★★★★</div><p>„Sehr professionelle Kanzlei. Die Beratung war verständlich, direkt und menschlich.“</p><small>Mandantenbewertung</small></article>
<article class="review" style="left:506px;top:2258px"><div class="q">99</div><div class="stars">★★★★★</div><p>„Kompetente Vertretung, schnelle Rückmeldung und ein sehr angenehmer Umgang.“</p><small>Online-Bewertung</small></article>
<article class="review" style="left:703px"><div class="q">99</div><div class="stars">★★★★★</div><p>„Ich habe mich jederzeit ernst genommen gefühlt. Absolute Empfehlung.“</p><small>Privatmandant</small></article>
<div class="arrow-btn" style="left:911px;background:var(--gold)"><svg width="8" height="8" viewBox="0 0 8 8" fill="none" stroke="#1b1a18"><path d="M3 1.5 5.5 4 3 6.5"/></svg></div>

<!-- Beiträge -->
<div class="abs eyebrow" style="left:262px;top:2614px">Aktuelles aus der Kanzlei</div>
<h2 class="abs display" style="left:262px;top:2631px">Beiträge mit<br>Orientierung.</h2>
<div class="abs card-grid" style="left:262px;top:2725px">
  <article class="post"><div class="img" role="img" aria-label="Foto einer Anwältin am Schreibtisch" style="background:linear-gradient(135deg,#d9d6d0,#6a665f)"></div><div class="date">▭ 12. APRIL 2026</div><h3>Was tun nach einer<br>Kündigung?</h3><p>Fristen, Unterlagen und die erste rechtliche Einschätzung entscheiden oft darüber, wie stark die eigene Position bleibt.</p><span class="btn btn-line">Weiterlesen ↗</span></article>
  <article class="post"><div class="img" role="img" aria-label="Foto des Empfangstresens der Kanzlei" style="background:linear-gradient(135deg,#4a4036,#8a6d4e 60%,#2b2621)"></div><div class="date">▭ 28. MÄRZ 2026</div><h3>Trennung mit klarer<br>Orientierung.</h3><p>Im Familienrecht helfen ruhige Beratung, Struktur und ein früher Überblick über Unterhalt, Sorge und Umgang.</p><span class="btn btn-line">Weiterlesen ↗</span></article>
  <article class="post"><div class="img" role="img" aria-label="Foto eines Besprechungsraums mit Wandbild" style="background:linear-gradient(135deg,#5a4a3a,#b3a48c 55%,#3a322a)"></div><div class="date">▭ 09. MÄRZ 2026</div><h3>Unfall, Bußgeld oder<br>Fahrverbot?</h3><p>Im Verkehrsrecht ist schnelles Handeln wichtig – besonders bei Fristen, Beweissicherung und Versicherungen.</p><span class="btn btn-line">Weiterlesen ↗</span></article>
</div>

<!-- CTA -->
<section class="abs band-dark" style="top:3084px;height:231px"></section>
<div class="abs eyebrow" style="left:262px;top:3131px">Erstkontakt</div>
<h2 class="abs display" style="left:262px;top:3148px;color:var(--white)">Klare Einschätzung?</h2>
<p class="abs" style="left:262px;top:3196px;width:320px;font-size:7.8px;color:#d4cdc1;line-height:1.8">Schildern Sie Ihr Anliegen kurz. Die Kanzlei am Lindenhof meldet sich zeitnah mit einer ersten Orientierung.</p>
<div class="abs" style="left:262px;top:3247px;display:flex;gap:6px">
  <span class="btn btn-dark">Termin anfragen <svg viewBox="0 0 8 8" fill="none" stroke="currentColor"><path d="M2 6 6 2M3 2h3v3"/></svg></span>
  <span class="btn btn-dark"><svg viewBox="0 0 8 8" fill="none" stroke="currentColor"><circle cx="4" cy="4" r="3.2"/></svg> Messenger</span>
</div>

<!-- Kontakt -->
<div class="abs eyebrow" style="left:262px;top:3490px">Kontakt &amp; Anfahrt</div>
<h2 class="abs display" style="left:262px;top:3508px">Kanzlei am Lindenhof.</h2>
<div class="abs" style="left:262px;top:3558px">
  <div class="contact-line"><svg viewBox="0 0 10 10" fill="none" stroke="#c8a96b"><path d="M5 9S1.8 5.8 1.8 3.9a3.2 3.2 0 0 1 6.4 0C8.2 5.8 5 9 5 9z"/><circle cx="5" cy="3.9" r="1.1"/></svg>Lindenstraße 14, 87435 Kempten</div>
  <div class="contact-line"><svg viewBox="0 0 10 10" fill="none" stroke="#c8a96b"><path d="M2 1.5h2l.8 2-1.2.9a5 5 0 0 0 2 2l.9-1.2 2 .8v2c0 .5-.5 1-1 1A7 7 0 0 1 1 2.5c0-.5.5-1 1-1z"/></svg>0831 / 54 02 721 0</div>
  <div class="contact-line"><svg viewBox="0 0 10 10" fill="none" stroke="#c8a96b"><rect x="1" y="2" width="8" height="6"/><path d="m1 2 4 3.3L9 2"/></svg>info@kanzlei-lindenhof.de</div>
</div>
<div class="abs" role="img" aria-label="Stadtplan von Kempten mit Lage der Kanzlei" style="left:589px;top:3425px;width:348px;height:243px;background:radial-gradient(ellipse at 50% 50%,#a9a6a0 0%,#8e8b86 70%,#7c7974 100%)"></div>
<div class="abs" style="left:605px;top:3625px;width:85px;height:30px;background:var(--ink);color:var(--white);padding:6px 8px 0 24px;font-size:7px;font-weight:600;line-height:1.3">Lindenstr. 14<br><span style="font-weight:400;font-size:5.5px;color:#cfc8bc">87435 Kempten</span></div>
<svg class="abs" style="left:614px;top:3631px" width="9" height="10" viewBox="0 0 10 10" fill="none" stroke="#c8a96b"><path d="M5 9S1.8 5.8 1.8 3.9a3.2 3.2 0 0 1 6.4 0C8.2 5.8 5 9 5 9z"/></svg>
<div class="abs" style="left:756px;top:3534px;width:12px;height:12px;border-radius:50%;background:var(--ink);border:3px solid var(--white)"></div>

<!-- Footer -->
<footer class="abs footer">
  <div class="abs brand" style="left:262px;top:46px;font-size:16px">KANZLEI LINDENHOF</div>
  <p class="abs" style="left:262px;top:74px;width:210px;font-size:7px;color:#d4cdc1;line-height:1.85">Rechtsanwälte in Kempten. Persönliche Beratung, klare Einschätzung und engagierte Vertretung für private und gewerbliche Mandanten.</p>
  <div class="abs" style="left:262px;top:140px;display:flex;gap:6px">
    <span class="btn btn-dark" style="height:21px;font-size:6.5px;padding:0 9px">Termin buchen ↗</span>
    <span class="btn btn-dark" style="height:21px;font-size:6.5px;padding:0 9px">○ Messenger</span>
  </div>
  <div class="abs" style="left:262px;top:171px"><span class="social"></span><span class="social"></span><span class="social"></span></div>
  <div class="fcol" style="left:500px"><h4>KONTAKT</h4>Lindenstraße 14<br>87435 Kempten<br>0831 / 54 02 721 0<br>info@kanzlei-lindenhof.de</div>
  <div class="fcol" style="left:663px"><h4>RECHTSGEBIETE</h4>Arbeitsrecht<br>Familienrecht<br>Verkehrsrecht<br>Strafrecht<br>Erbrecht<br>Mietrecht</div>
  <div class="fcol" style="left:828px"><h4>NAVIGATION</h4>Startseite<br>Rechtsgebiete<br>Kanzlei<br>Bewertungen<br>Kontakt</div>
  <div class="abs" style="left:262px;top:208px;width:675px;height:1px;background:rgba(255,255,255,.1)"></div>
  <div class="abs" style="left:262px;top:216px;font-size:6.5px;color:#a8a196">© 2026 Kanzlei am Lindenhof</div>
  <div class="abs" style="left:858px;top:216px;font-size:6.5px;color:#a8a196">Impressum · Datenschutz</div>
</footer>

</body>
</html>
```